TalkHarbor - Language Coaching Services

Sleek, innovative, trendy design for Language Coaching business.

TalkHarbor is a new UK based company that provides Language Coaching services. We offer highly personalized on-line and face to face language courses. We also impart learning techniques workshops based on the latest neuroscience research for second-language acquisition.

Target Market(s)

See attached info

Industry/Entity Type

Consulting

Contact Information for Business Card

TalkHarbor
DaniaKV@talkharbor.co.uk
TalkHarbor.co.uk
London, UK

Font styles to use
Sans Serif

```html
<!DOCTYPE html>
<html lang="en">
<head>
<meta charset="utf-8">
<title>TalkHarbor Business Card</title>
<link rel="stylesheet" href="https://fonts.googleapis.com/css2?family=Montserrat:wght@500&family=Roboto:wght@400;500;700&display=swap">
<style>
  :root {
    --stage: #2b2c2e;
    --card-dark: #1c1d1f;
    --card-light: #ffffff;
    --brand-blue: #1a8fc6;
    --accent-blue: #14a9e4;
    --text-light: #ffffff;
    --text-muted: #c9cbcd;
  }
  * { box-sizing: border-box; margin: 0; padding: 0; }
  html, body {
    width: 1200px;
    height: 960px;
    overflow: hidden;
    background: var(--stage);
  }
  .stage {
    position: relative;
    width: 1200px;
    height: 960px;
  }
  .card {
    position: absolute;
    left: 250px;
    width: 700px;
    height: 400px;
    overflow: hidden;
    box-shadow: 0 12px 30px rgba(0, 0, 0, 0.45);
  }
  .card--back {
    top: 60px;
    background: var(--card-dark);
  }
  .card--front {
    top: 500px;
    background: var(--card-light);
  }

  /* Back side */
  .back-brand {
    position: absolute;
    left: 0;
    top: 0;
    width: 100%;
    height: 100%;
    display: flex;
    align-items: center;
    justify-content: center;
    gap: 26px;
  }
  .brand-ring {
    width: 150px;
    height: 150px;
    border-radius: 50%;
    border: 12px solid var(--brand-blue);
    flex: none;
  }
  .brand-name {
    font-family: "Montserrat", sans-serif;
    font-weight: 500;
    color: var(--brand-blue);
    letter-spacing: 1px;
  }
  .back-brand .brand-name { font-size: 40px; }
  .back-url {
    position: absolute;
    left: 0;
    right: 0;
    bottom: 70px;
    text-align: center;
    font-family: "Roboto", sans-serif;
    font-size: 15px;
    letter-spacing: 4px;
    color: var(--text-muted);
  }

  /* Front side */
  .front-brand {
    position: absolute;
    left: 70px;
    top: 95px;
    display: flex;
    flex-direction: column;
    align-items: center;
    gap: 18px;
  }
  .front-brand .brand-ring {
    width: 100px;
    height: 100px;
    border-width: 8px;
  }
  .front-brand .brand-name { font-size: 44px; }
  .front-swoosh {
    position: absolute;
    left: 0;
    top: 0;
    width: 700px;
    height: 400px;
  }
  .contact {
    position: absolute;
    right: 24px;
    top: 185px;
    text-align: right;
    font-family: "Roboto", sans-serif;
    color: var(--text-light);
  }
  .contact-name {
    font-size: 22px;
    font-weight: 700;
    letter-spacing: 0.5px;
    line-height: 26px;
    margin-right: 28px;
  }
  .contact-title {
    font-size: 14px;
    font-weight: 500;
    margin: 2px 28px 14px 0;
  }
  .contact-list { list-style: none; }
  .contact-row {
    display: flex;
    align-items: center;
    justify-content: flex-end;
    gap: 10px;
    font-size: 16px;
    line-height: 24px;
  }
  .contact-icon {
    width: 18px;
    height: 18px;
    flex: none;
  }
</style>
</head>
<body>
<main class="stage">

  <section class="card card--back" aria-label="Card back">
    <div class="back-brand">
      <span class="brand-ring" aria-hidden="true"></span>
      <span class="brand-name">TALKHARBOR</span>
    </div>
    <p class="back-url">talkharbor.co.uk</p>
  </section>

  <section class="card card--front" aria-label="Card front">
    <svg class="front-swoosh" viewBox="0 0 700 400" aria-hidden="true">
      <circle cx="760" cy="420" r="360" fill="var(--accent-blue)"/>
      <circle cx="760" cy="420" r="350" fill="none" stroke="var(--text-light)" stroke-width="2"/>
      <path d="M392 400 A368 368 0 0 1 608 85" fill="none" stroke="var(--brand-blue)" stroke-width="2"/>
      <path d="M600 80 L630 78 L606 96 Z" fill="var(--brand-blue)"/>
    </svg>

    <div class="front-brand">
      <span class="brand-ring" aria-hidden="true"></span>
      <span class="brand-name">TALKHARBOR</span>
    </div>

    <div class="contact">
      <p class="contact-name">OWEN HALE</p>
      <p class="contact-title">CEO/FOUNDER</p>
      <ul class="contact-list">
        <li class="contact-row">
          <span>020 7946 0321</span>
          <svg class="contact-icon" viewBox="0 0 18 18" aria-label="Phone">
            <rect x="5" y="1" width="8" height="16" rx="1.5" fill="none" stroke="var(--text-light)" stroke-width="1.5"/>
            <circle cx="9" cy="14" r="1" fill="var(--text-light)"/>
          </svg>
        </li>
        <li class="contact-row">
          <span>info@talkharbor.co.uk</span>
          <svg class="contact-icon" viewBox="0 0 18 18" aria-label="Email">
            <rect x="1" y="4" width="16" height="11" rx="1" fill="var(--text-light)"/>
            <path d="M1.5 4.5 L9 10.5 L16.5 4.5" fill="none" stroke="var(--accent-blue)" stroke-width="1.4"/>
          </svg>
        </li>
        <li class="contact-row">
          <span>www.talkharbor.co.uk</span>
          <svg class="contact-icon" viewBox="0 0 18 18" aria-label="Website">
            <circle cx="9" cy="9" r="7.5" fill="var(--text-light)"/>
            <path d="M1.5 9 H16.5 M9 1.5 C5.5 5 5.5 13 9 16.5 M9 1.5 C12.5 5 12.5 13 9 16.5" fill="none" stroke="var(--accent-blue)" stroke-width="1.2"/>
          </svg>
        </li>
      </ul>
    </div>
  </section>

</main>
</body>
</html>
```